BildeVOLD buisnesscard

Hey :) I need a modern buisnesscard for my company BildeVOLD
It most have:
Dagligleder og Fotograf: Henrik Audun Strandvik

Mob: +4791264085
Epost: post@bildevold.example
Adresse: Kvernbakken9, 6040 Langevåg

Facbook and instagram logo with text BildeVOLD

BildeVOLD logo

It Company

```html
<!DOCTYPE html>
<html lang="no">
<head>
<meta charset="utf-8">
<title>BildeVOLD – visittkort</title>
<link href="https://fonts.googleapis.com/css2?family=Ubuntu:wght@400;500;700&display=swap" rel="stylesheet">
<style>
  :root {
    --page-bg: #ecebe8;
    --card-white: #ffffff;
    --panel-blue: #2b86bf;
    --panel-blue-light: #3fa0d4;
    --ink-dark: #26313d;
    --rule: #b9c3cc;
    --text-light: #ffffff;
  }
  * { box-sizing: border-box; margin: 0; padding: 0; }
  html, body {
    width: 1200px; height: 950px; overflow: hidden;
    background: var(--page-bg);
    font-family: "Ubuntu", sans-serif;
  }
  .sheet {
    width: 1200px; height: 950px;
    display: flex; justify-content: center; align-items: center; gap: 90px;
  }
  .card {
    width: 440px; height: 770px;
    background: var(--card-white);
    position: relative;
    box-shadow: 0 6px 24px rgba(0,0,0,.18);
    overflow: hidden;
  }

  /* Front */
  .card-front .info-panel {
    position: absolute; top: 0; left: 44px; right: 0; height: 470px;
    background: linear-gradient(160deg, var(--panel-blue-light), var(--panel-blue));
    color: var(--text-light);
    text-align: right;
    padding: 30px 34px 0 0;
  }
  .holder-name { font-weight: 700; font-size: 25px; letter-spacing: .3px; }
  .holder-title { font-size: 19px; margin-top: 4px; }
  .contact-list { list-style: none; margin-top: 30px; font-size: 18px; line-height: 1.45; }
  .contact-list .icon {
    display: inline-block; width: 15px; height: 15px; margin-right: 7px;
    vertical-align: -2px;
  }
  .brand-name-front {
    position: absolute; left: 44px; bottom: 160px;
    font-weight: 500; font-size: 52px; color: var(--ink-dark);
    text-transform: uppercase; letter-spacing: 2px;
  }

  /* Back */
  .card-back .brand-block {
    position: absolute; top: 300px; left: 0; right: 0;
    display: flex; justify-content: center; align-items: center; gap: 14px;
  }
  .brand-dot { width: 18px; height: 18px; border-radius: 50%; background: var(--ink-dark); }
  .brand-name-back {
    font-weight: 500; font-size: 42px; color: var(--ink-dark);
    text-transform: uppercase; letter-spacing: 2px;
  }
  .social-row {
    position: absolute; bottom: 110px; left: 50px; right: 50px;
    display: flex; align-items: center; gap: 8px;
  }
  .social-row .rule { flex: 1; height: 1px; background: var(--rule); }
  .social-dot {
    width: 26px; height: 26px; border-radius: 50%;
    border: 1.5px solid var(--ink-dark);
  }
</style>
</head>
<body>
<main class="sheet">
  <section class="card card-front" aria-label="Visittkort forside">
    <div class="info-panel">
      <h1 class="holder-name">Henrik Audun Strandvik</h1>
      <p class="holder-title">Dagligleder og Fotograf</p>
      <ul class="contact-list">
        <li>Kvernbakken 9</li>
        <li>6040 Langevåg</li>
        <li>
          <svg class="icon" viewBox="0 0 16 16"><rect x="4" y="1" width="8" height="14" rx="1.5" fill="none" stroke="#fff" stroke-width="1.6"/><circle cx="8" cy="12.3" r=".9" fill="#fff"/></svg>+4791264085
        </li>
        <li>
          <svg class="icon" viewBox="0 0 16 16"><rect x="1" y="3" width="14" height="10" rx="1" fill="#fff"/><path d="M1.5 3.5 8 9l6.5-5.5" fill="none" stroke="#2b86bf" stroke-width="1.3"/></svg>post@bildevold.example
        </li>
        <li>
          <svg class="icon" viewBox="0 0 16 16"><circle cx="8" cy="8" r="6.5" fill="none" stroke="#fff" stroke-width="1.5"/><ellipse cx="8" cy="8" rx="2.8" ry="6.5" fill="none" stroke="#fff" stroke-width="1.2"/><path d="M1.5 8h13" stroke="#fff" stroke-width="1.2"/></svg>www.bildevold.example
        </li>
      </ul>
    </div>
    <p class="brand-name-front">BildeVOLD</p>
  </section>

  <section class="card card-back" aria-label="Visittkort bakside">
    <div class="brand-block">
      <span class="brand-dot"></span>
      <span class="brand-name-back">BildeVOLD</span>
    </div>
    <div class="social-row" aria-label="Sosiale medier: BildeVOLD">
      <span class="rule"></span>
      <span class="social-dot"></span>
      <span class="social-dot"></span>
      <span class="rule"></span>
    </div>
  </section>
</main>
</body>
</html>
```